Corvane Holdings , new business card design

investment firm with corporate clients . need double sided business card , vertical and horizontal options ,logo must be clear. prefer pantone colors only and sharp design. website also www.corvane.ae

Khalid Bin Tarrafi
Managing Director
Tel. +971 4 387 2940
Mobile +971 50 518 2403
khalid@corvane.ae
Q-Span Plaza, officw 18-B07, Warqa Gardens, Dubai

Contact Information for Business Card

Khalid Bin Tarrafi
Managing Director

Font styles to use
Serif

Colors

Designer to choose colors to be used in the design.

```html
<!DOCTYPE html>
<html lang="en">
<head>
<meta charset="utf-8">
<title>Corvane Holdings – Business Card</title>
<link rel="stylesheet" href="https://fonts.googleapis.com/css2?family=Roboto:wght@300;400&family=Roboto+Condensed:wght@400;700&display=swap">
<style>
  :root {
    --stage: #e9e7e3;
    --paper: #fbfbfa;
    --ink: #1f2226;
    --steel: #4f7aa3;
    --logo-grey: #3a3f45;
    --night: #0c0d12;
    --white: #ffffff;
  }
  * { margin: 0; padding: 0; box-sizing: border-box; }
  html, body { width: 1200px; height: 886px; overflow: hidden; }
  body {
    background: var(--stage);
    font-family: "Roboto", Arial, sans-serif;
    position: relative;
  }
  .card {
    position: absolute;
    top: 288px;
    width: 530px;
    height: 310px;
    box-shadow: 0 6px 18px rgba(0,0,0,0.18);
  }
  .card--front { left: 50px; background: var(--paper); }
  .card--back { left: 620px; background: var(--night); }

  .wordmark {
    position: absolute;
    display: flex;
    align-items: center;
    gap: 10px;
    font-family: "Roboto", Arial, sans-serif;
    font-weight: 300;
    text-transform: uppercase;
    white-space: nowrap;
  }
  .wordmark__square { width: 12px; height: 12px; flex: none; }
  .card--front .wordmark {
    left: 30px; top: 86px;
    font-size: 26px; letter-spacing: 7px;
    color: var(--logo-grey);
  }
  .card--front .wordmark__square { background: var(--steel); }
  .card--back .wordmark {
    left: 50%; top: 50%;
    transform: translate(-50%, -50%);
    font-size: 28px; letter-spacing: 8px;
    color: var(--white);
  }
  .card--back .wordmark__square { background: var(--white); }

  .holder { position: absolute; left: 30px; top: 136px; }
  .holder__name {
    font-family: "Roboto Condensed", Arial, sans-serif;
    font-weight: 700; font-size: 19px;
    color: var(--steel); line-height: 22px;
  }
  .holder__title {
    font-family: "Roboto Condensed", Arial, sans-serif;
    font-weight: 400; font-size: 14px;
    color: var(--ink); line-height: 18px;
  }
  .address {
    position: absolute; left: 30px; top: 184px;
    font-size: 12px; line-height: 16px; color: var(--ink);
  }
  .contacts {
    position: absolute; left: 30px; top: 222px;
    list-style: none;
    font-size: 12px; line-height: 15px; color: var(--ink);
  }
  .contacts li { display: flex; align-items: center; gap: 7px; }
  .contacts svg { width: 10px; height: 10px; flex: none; }

  .rule {
    position: absolute; left: 24px; right: 0; top: 282px;
    height: 1px; background: var(--steel);
  }
  .web-tag {
    position: absolute; right: 24px; top: 258px;
    height: 24px; padding: 0 14px;
    background: var(--steel); color: var(--white);
    font-size: 12px; letter-spacing: 4px; line-height: 24px;
  }
</style>
</head>
<body>
  <section class="card card--front" aria-label="Card front">
    <div class="wordmark"><span class="wordmark__square"></span>Corvane Holdings</div>
    <div class="holder">
      <p class="holder__name">Khalid Bin Tarrafi</p>
      <p class="holder__title">Managing Director</p>
    </div>
    <p class="address">Q-Span Plaza, officw 18-B07<br>Warqa Gardens, Dubai</p>
    <ul class="contacts">
      <li>
        <svg viewBox="0 0 10 10" aria-hidden="true"><path d="M2 1 L4 3 L3 4.3 Q4.5 6 5.7 7 L7 6 L9 8 L7.6 9.4 Q4 9 0.6 2.4 Z" fill="var(--steel)"/></svg>
        +971 4 387 2940
      </li>
      <li>
        <svg viewBox="0 0 10 10" aria-hidden="true"><rect x="2.5" y="0.5" width="5" height="9" rx="1" fill="none" stroke="var(--steel)" stroke-width="1.2"/></svg>
        +971 50 518 2403
      </li>
      <li>
        <svg viewBox="0 0 10 10" aria-hidden="true"><rect x="0.5" y="1.5" width="9" height="7" fill="var(--steel)"/><path d="M0.5 1.5 L5 5.5 L9.5 1.5" fill="none" stroke="var(--paper)" stroke-width="1"/></svg>
        khalid@corvane.ae
      </li>
    </ul>
    <div class="rule"></div>
    <div class="web-tag">www.corvane.ae</div>
  </section>

  <section class="card card--back" aria-label="Card back">
    <div class="wordmark"><span class="wordmark__square"></span>Corvane Holdings</div>
  </section>
</body>
</html>
```